Flat Belly Design Graphics for Social

I want to create 9 social media graphics (new Instagram size 4:5 (1080 x 1350 pixels) focusing on our Flat Belly Graphics, using the pics attached. Use the attached pics, NO RANDOM STOCK PHOTOGRAPHY. For the color scheme of the graphics, the color palette is attached. YOU MUST POST ALL 9 GRAPHICS IN ONE ENTRY.
Using the 3 titles below, create one set of graphics. 1) with all text, then for the others, use the pictures as detailed below in IMPORTANT:
1. Ten-Week Bright Morning Reboot
2. The Quick Garden Kitchen Menu Guide
3. Studio Habits for Lasting Energy Past Midlife - Zero Gym Needed
IMPORTANT:
Only use RK Pic 1 and RK Pic 2 with the title, Ten-Week Bright Morning Reboot
Only use meal plan1 and meal plan2 pics with the title, Quick Garden Kitchen Menu Guide
Only use studio habits 1 and studio habits 2 pics with the title, Studio Habits for Lasting Energy Past Midlife - Zero Gym Needed
women over 40

```html
<!DOCTYPE html>
<html lang="en">
<head>
<meta charset="utf-8">
<title>Flat Belly Social Set</title>
<link rel="stylesheet" href="https://fonts.googleapis.com/css2?family=Oswald:wght@600;700&family=Archivo:wdth,wght@125,900&family=Lexend:wght@500;600&family=Great+Vibes&display=swap">
<style>
:root{
  --stage:#444444;
  --green:#1b5a52;
  --pink:#cf5b93;
  --pink-bright:#ee86ad;
  --pink-mid:#e49ab5;
  --blush:#fbe4ea;
  --blush-deep:#f7dbe2;
  --white:#ffffff;
}
*{margin:0;padding:0;box-sizing:border-box}
html,body{width:960px;height:1200px;overflow:hidden;background:var(--stage)}
.canvas{position:relative;width:960px;height:1200px}
.card{position:absolute;width:231px;height:289px;overflow:hidden;background:var(--blush)}
.col-1{left:110px}.col-2{left:363px}.col-3{left:616px}
.row-1{top:132px}.row-2{top:452px}.row-3{top:772px}
.abs{position:absolute;white-space:nowrap}
.center{left:0;right:0;text-align:center}
.cond{font-family:"Oswald",sans-serif;font-weight:700;letter-spacing:-.5px;line-height:1}
.wide{font-family:"Archivo",sans-serif;font-weight:900;font-stretch:125%;line-height:1}
.sans{font-family:"Lexend",sans-serif;font-weight:600;line-height:1}
.script{font-family:"Great Vibes",cursive;line-height:1}
.green{color:var(--green)}.pink{color:var(--pink)}.bright{color:var(--pink-bright)}.white{color:var(--white)}
.photo{position:absolute}

/* card 1 */
.slant-band{position:absolute;background:var(--green);transform:skewX(-14deg)}
.slant-tag{position:absolute;background:var(--pink);transform:skewX(-14deg)}
.rule{position:absolute;height:4px;background:var(--pink)}

/* card 2 / 8 */
.menu-box{position:absolute;left:9px;right:9px;background:var(--green)}
.menu-box .frame{position:absolute;inset:5px;border:1px solid rgba(255,255,255,.8);border-radius:8px}

/* card 3 */
.habit-box{position:absolute;left:11px;right:17px;background:var(--green)}

/* card 4 */
.title-panel{position:absolute;left:10px;right:11px;top:180px;bottom:9px;background:var(--blush);border-radius:16px}

/* card 7 */
.pill{position:absolute;left:16px;right:12px;top:6px;height:45px;background:var(--green);border-radius:24px}
.vert{position:absolute;top:62px;width:30px;display:flex;flex-direction:column;align-items:center;font-family:"Archivo",sans-serif;font-weight:900;font-stretch:125%;color:var(--pink);line-height:1.08}
.reboot-box{position:absolute;left:15px;right:15px;top:217px;height:61px;background:var(--pink)}
</style>
</head>
<body>
<main class="canvas">

  <!-- Row 1 -->
  <section class="card col-1 row-1">
    <div class="slant-band" style="left:18px;top:36px;width:200px;height:42px"></div>
    <div class="abs center wide white" style="top:42px;font-size:30px">TEN-WEEK</div>
    <div class="abs center cond pink" style="top:88px;font-size:42px">BRIGHT</div>
    <div class="abs center cond green" style="top:140px;font-size:46px">MORNING</div>
    <div class="rule" style="left:0;top:223px;width:60px"></div>
    <div class="rule" style="right:0;top:228px;width:54px"></div>
    <div class="slant-tag" style="left:52px;top:204px;width:128px;height:55px"></div>
    <div class="abs center wide white" style="top:221px;font-size:20px">REBOOT</div>
  </section>

  <section class="card col-2 row-1">
    <div class="abs center cond green" style="top:28px;font-size:36px">THE QUICK</div>
    <div class="abs center cond pink" style="top:84px;font-size:30px">GARDEN KITCHEN</div>
    <div class="menu-box" style="top:145px;height:123px"><div class="frame"></div></div>
    <div class="abs center wide white" style="top:160px;font-size:40px">MENU</div>
    <div class="abs center wide white" style="top:214px;font-size:40px">GUIDE</div>
  </section>

  <section class="card col-3 row-1">
    <div class="abs center script pink" style="top:30px;font-size:26px">Studio Habits</div>
    <div class="abs center cond green" style="top:66px;font-size:22px">FOR LASTING ENERGY</div>
    <div class="abs center cond bright" style="top:96px;font-size:34px">PAST MIDLIFE</div>
    <div class="habit-box" style="top:150px;height:110px"></div>
    <div class="abs cond white" style="left:11px;right:17px;top:162px;text-align:center;font-size:34px">ZERO GYM</div>
    <div class="abs cond white" style="left:11px;right:17px;top:208px;text-align:center;font-size:34px">NEEDED</div>
  </section>

  <!-- Row 2 -->
  <section class="card col-1 row-2" style="background:var(--pink-mid)">
    <div class="photo" role="img" aria-label="Photo of a smiling woman in a white cropped sweater pointing to her midsection" style="inset:0 0 100px 0;background:radial-gradient(circle at 50% 35%,#f7d7e2 0%,#eaaac1 45%,#e49ab5 75%)"></div>
    <div class="title-panel"></div>
    <div class="abs sans green" style="left:10px;right:11px;top:194px;text-align:center;font-size:22px">TEN-WEEK</div>
    <div class="abs sans pink" style="left:10px;right:11px;top:224px;text-align:center;font-size:14px;font-weight:500;letter-spacing:1.5px;opacity:.75">BRIGHT MORNING</div>
    <div class="abs sans green" style="left:10px;right:11px;top:244px;text-align:center;font-size:24px;letter-spacing:-.5px">REBOOT</div>
  </section>

  <section class="card col-2 row-2" style="background:var(--green)">
    <div class="abs center sans white" style="top:24px;font-size:24px">THE QUICK</div>
    <div class="abs center sans" style="top:58px;font-size:19px;color:var(--pink-mid)">GARDEN KITCHEN</div>
    <div class="abs center sans white" style="top:96px;font-size:26px">MENU GUIDE</div>
    <div class="photo" role="img" aria-label="Overhead photo of chicken, berries, vegetables, grains and a meal planning sheet on a wooden table" style="left:0;right:0;top:133px;bottom:0;background:linear-gradient(135deg,#8a5a3c 0%,#c9a57e 35%,#7d9a55 60%,#b2472f 80%,#5e3a26 100%)"></div>
  </section>

  <section class="card col-3 row-2">
    <div class="photo" role="img" aria-label="Photo of one woman whispering a secret to a delighted friend" style="left:0;right:0;top:0;height:189px;background:linear-gradient(135deg,#5a3a2c 0%,#c99a82 40%,#f2e6e2 70%,#8a6a5a 100%)"></div>
    <div class="abs center sans green" style="top:197px;font-size:14px">STUDIO HABITS</div>
    <div class="abs center script pink" style="top:213px;font-size:17px">for Lasting Energy</div>
    <div class="abs center sans bright" style="top:233px;font-size:23px">PAST MIDLIFE</div>
    <div class="abs center cond green" style="top:262px;font-size:19px">ZERO GYM NEEDED</div>
  </section>

  <!-- Row 3 -->
  <section class="card col-1 row-3">
    <div class="pill"></div>
    <div class="abs sans white" style="left:16px;right:12px;top:11px;text-align:center;font-size:30px">TEN-WEEK</div>
    <div class="vert" style="left:12px;font-size:21px"><span>B</span><span>R</span><span>I</span><span>G</span><span>H</span><span>T</span></div>
    <div class="vert" style="right:10px;font-size:18px;line-height:1.05"><span>M</span><span>O</span><span>R</span><span>N</span><span>I</span><span>N</span><span>G</span></div>
    <div class="photo" role="img" aria-label="Photo of a smiling woman in a white cropped sweater pointing to her midsection" style="left:56px;right:56px;top:58px;height:158px;background:linear-gradient(180deg,#fbe4ea 0%,#f0e8ea 50%,#3a3030 85%,#222 100%)"></div>
    <div class="reboot-box"></div>
    <div class="abs sans white" style="left:15px;right:15px;top:235px;text-align:center;font-size:26px">REBOOT</div>
  </section>

  <section class="card col-2 row-3" style="background:var(--blush-deep)">
    <div class="abs center script green" style="top:34px;font-size:32px">The Quick</div>
    <div class="abs center cond pink" style="top:86px;font-size:30px">GARDEN KITCHEN</div>
    <div class="menu-box" role="img" aria-label="Soft photo of fresh vegetables and a meal planning sheet behind the title" style="top:145px;height:123px;background:linear-gradient(135deg,#2f5a4a 0%,#4d7a5a 40%,#2b4f45 70%,#5a7a4a 100%)"><div class="frame"></div></div>
    <div class="abs center wide white" style="top:160px;font-size:40px">MENU</div>
    <div class="abs center wide white" style="top:214px;font-size:40px">GUIDE</div>
  </section>

  <section class="card col-3 row-3" style="background:var(--blush-deep)">
    <div class="photo" role="img" aria-label="Photo of a woman whispering to a surprised friend" style="left:96px;right:0;top:40px;bottom:0;background:linear-gradient(90deg,rgba(247,219,226,0) 0%,#e8c0b5 25%,#c9917e 55%,#6a4a3e 85%,#a8c0d8 100%)"></div>
    <div class="abs sans green" style="left:10px;top:20px;font-size:20px">STUDIO</div>
    <div class="abs sans green" style="left:10px;top:44px;font-size:16px">HABITS FOR</div>
    <div class="abs script pink" style="left:11px;top:86px;font-size:18px">Lasting Energy</div>
    <div class="abs sans bright" style="left:11px;top:108px;font-size:22px">PAST</div>
    <div class="abs sans bright" style="left:8px;top:138px;font-size:32px">MIDLIFE</div>
    <div class="abs sans green" style="left:12px;top:200px;font-size:18px">ZERO</div>
    <div class="abs sans green" style="left:12px;top:224px;font-size:18px">GYM</div>
    <div class="abs sans green" style="left:12px;top:248px;font-size:18px">NEEDED</div>
  </section>

</main>
</body>
</html>
```